Veranix - Solution provider in business consulting

Veranix is a swiss based company providing solutions for developing markets. The business covers various fields of business consulting, such as supply chain, product costs, quality management and manufacturing management. The Business operates in a efficient, straight and solution oriented manner.
The final design should communicate these characteristics. Asian people as well as as western people shall identify the qualities of the company at first sight.
The customer needs business cards with a simple view but an recognizable design, printed in high quality. Engraved elements such as the globe or simple words are possible.
Available colors are: (RAL)
102/102/102
51/102/102
153/204/153
255/102/51
Font: Calibri

```html
<!DOCTYPE html>
<html lang="en">
<head>
<meta charset="utf-8">
<title>Veranix Business Card</title>
<link rel="stylesheet" href="https://fonts.googleapis.com/css2?family=Carlito:wght@400;700&display=swap">
<style>
  :root {
    --paper: #ffffff;
    --edge-teal: #52a8b0;
    --logo-panel: #93d7f5;
    --card-blue: #7bc4dc;
    --ink-navy: #0d2a63;
    --brand-grey: #666666;
    --crop-line: #222222;
  }
  html, body {
    margin: 0;
    padding: 0;
    width: 1200px;
    height: 843px;
    overflow: hidden;
    background: var(--paper);
  }
  .sheet {
    position: relative;
    width: 1200px;
    height: 843px;
    font-family: "Carlito", Calibri, Arial, sans-serif;
  }
  .crop-marks {
    position: absolute;
    inset: 0;
  }
  .card {
    position: absolute;
    left: 98px;
    top: 135px;
    width: 1002px;
    height: 573px;
    background: var(--card-blue);
  }
  .edge-strip {
    position: absolute;
    top: 0;
    height: 100%;
    background: var(--edge-teal);
  }
  .edge-strip--left { left: 0; width: 30px; }
  .edge-strip--right { left: 973px; width: 29px; }
  .brand-panel {
    position: absolute;
    left: 30px;
    top: 0;
    width: 244px;
    height: 100%;
    background: var(--logo-panel);
    display: flex;
    align-items: center;
    justify-content: center;
  }
  .brand-name {
    font-size: 48px;
    font-weight: 400;
    color: var(--brand-grey);
    line-height: 1;
    white-space: nowrap;
  }
  .contact {
    position: absolute;
    right: 122px;
    top: 81px;
    text-align: right;
    color: var(--ink-navy);
    font-size: 35px;
    line-height: 36px;
    white-space: nowrap;
  }
  .contact p { margin: 0; }
  .contact-block + .contact-block { margin-top: 28px; }
  .person-name { font-weight: 700; }
</style>
</head>
<body>
<div class="sheet">
  <svg class="crop-marks" width="1200" height="843" viewBox="0 0 1200 843" aria-hidden="true">
    <g stroke="var(--crop-line)" stroke-width="1">
      <line x1="84" y1="0" x2="84" y2="72"/>
      <line x1="117" y1="35" x2="117" y2="93"/>
      <line x1="0" y1="83" x2="72" y2="83"/>
      <line x1="35" y1="116" x2="93" y2="116"/>

      <line x1="1116" y1="0" x2="1116" y2="72"/>
      <line x1="1083" y1="35" x2="1083" y2="93"/>
      <line x1="1128" y1="83" x2="1200" y2="83"/>
      <line x1="1107" y1="116" x2="1165" y2="116"/>

      <line x1="84" y1="771" x2="84" y2="843"/>
      <line x1="117" y1="750" x2="117" y2="808"/>
      <line x1="0" y1="759" x2="72" y2="759"/>
      <line x1="35" y1="725" x2="93" y2="725"/>

      <line x1="1116" y1="771" x2="1116" y2="843"/>
      <line x1="1083" y1="750" x2="1083" y2="808"/>
      <line x1="1128" y1="759" x2="1200" y2="759"/>
      <line x1="1107" y1="725" x2="1165" y2="725"/>
    </g>
  </svg>

  <div class="card">
    <div class="edge-strip edge-strip--left"></div>
    <div class="brand-panel">
      <span class="brand-name">Veranix</span>
    </div>
    <div class="edge-strip edge-strip--right"></div>

    <div class="contact">
      <div class="contact-block">
        <p class="person-name">Marco Lindt</p>
        <p class="person-role">CEO</p>
      </div>
      <div class="contact-block">
        <p>Veranix GmbH</p>
        <p>Talweg 14</p>
        <p>9240 Feldmoos</p>
        <p>Switzerland</p>
      </div>
      <div class="contact-block">
        <p>Mobile +41 79 000 1234</p>
        <p>Phone +41 71 000 5678</p>
        <p>marco.lindt@veranix.ch</p>
        <p>www.veranix.ch</p>
      </div>
    </div>
  </div>
</div>
</body>
</html>
```